Retail swing tag labels for a sale / reduction

We need some graphics done to be made into retail swing tag labels, for the purpose of reductions on selected products.

We have attached 2 examples of previous designs that were similar idea, but more themed for 'autumn' and 'winter'. This theme will just have the word 'REDUCED'.

The white areas can be smaller in size, as we would like to include a large "20% OFF" at the bottom, and then a 30%, 40%, 50% option.

Overall colour scheme should be red background with some form of detailed patterning (see previous examples). Bright and e-catching.

Any other questions, just ask.

The screenshot is front the printers, but in horizontal orientation.

The finished dimensions will be A6 portrait, printed both sides.

We have also included the vector file of the shop "Hollowmere Furnishings", which can be included on 1 of the sides.

```html
<!DOCTYPE html>
<html lang="en">
<head>
<meta charset="utf-8">
<title>Reduced 20% Off – Swing Tag</title>
<link rel="stylesheet" href="https://fonts.googleapis.com/css2?family=Anton&family=Montserrat:wght@400;700&display=swap">
<style>
  :root {
    --tag-red: #d8232f;
    --tag-red-light: #e0333a;
    --tag-red-deep: #b8121f;
    --shadow-red: #b01020;
    --band-white: #ffffff;
    --offer-red: #d81b2b;
    --offer-shadow: #f5cfc4;
    --rule-blue: #3a4a9a;
    --rule-green: #2a9a4a;
  }
  html, body {
    margin: 0;
    padding: 0;
    overflow: hidden;
    background: #ffffff;
  }
  .swing-tag {
    position: relative;
    width: 859px;
    height: 1200px;
    overflow: hidden;
    background: var(--band-white);
  }
  .red-panel {
    position: absolute;
    left: 0;
    width: 859px;
    background: radial-gradient(ellipse at 50% 50%, var(--tag-red-light) 0%, var(--tag-red) 60%, #d11f2c 100%);
  }
  .red-panel--top { top: 0; height: 355px; }
  .red-panel--bottom {
    top: 846px;
    height: 354px;
    background:
      linear-gradient(to bottom, rgba(120,0,10,0.45) 0px, rgba(120,0,10,0) 24px),
      radial-gradient(ellipse at 50% 50%, var(--tag-red-light) 0%, var(--tag-red) 60%, #d11f2c 100%);
  }
  .tag-rules {
    position: absolute;
    inset: 0;
  }
  .headline, .offer, .brand-name {
    position: absolute;
    left: 0;
    top: 0;
  }
</style>
</head>
<body>
<main class="swing-tag">
  <div class="red-panel red-panel--top" role="img" aria-label="Red background with detailed geometric patterning"></div>
  <div class="red-panel red-panel--bottom" role="img" aria-label="Red background with detailed geometric patterning"></div>

  <svg class="tag-rules" width="859" height="1200" viewBox="0 0 859 1200" aria-hidden="true">
    <g fill="none" stroke-width="1.2">
      <path d="M16 355 V16 H843 V355" stroke="var(--rule-blue)"/>
      <path d="M24 355 V24 H835 V355" stroke="var(--rule-green)"/>
      <path d="M16 846 V1184 H843 V846" stroke="var(--rule-blue)"/>
      <path d="M24 846 V1176 H835 V846" stroke="var(--rule-green)"/>
    </g>
  </svg>

  <svg class="headline" width="859" height="355" viewBox="0 0 859 355">
    <text x="95" y="355" textLength="697" lengthAdjust="spacingAndGlyphs"
          font-family="Anton, sans-serif" font-size="258" fill="var(--shadow-red)">REDUCED</text>
    <text x="81" y="355" textLength="697" lengthAdjust="spacingAndGlyphs"
          font-family="Anton, sans-serif" font-size="258" fill="var(--band-white)">REDUCED</text>
  </svg>

  <svg class="offer" width="859" height="846" viewBox="0 0 859 846">
    <text x="441" y="651" text-anchor="middle" textLength="596" lengthAdjust="spacingAndGlyphs"
          font-family="Montserrat, sans-serif" font-weight="700" font-size="296" fill="var(--offer-shadow)">20%</text>
    <text x="431" y="641" text-anchor="middle" textLength="596" lengthAdjust="spacingAndGlyphs"
          font-family="Montserrat, sans-serif" font-weight="700" font-size="296" fill="var(--offer-red)">20%</text>
    <text x="428" y="794" text-anchor="middle" textLength="324" lengthAdjust="spacingAndGlyphs"
          font-family="Montserrat, sans-serif" font-weight="700" font-size="156" fill="var(--offer-red)">OFF</text>
  </svg>

  <svg class="brand-name" width="859" height="1200" viewBox="0 0 859 1200">
    <rect x="405" y="968" width="48" height="48" fill="none" stroke="var(--band-white)" stroke-width="1.4"/>
    <text x="430" y="1110" text-anchor="middle" textLength="560" lengthAdjust="spacing"
          font-family="Montserrat, sans-serif" font-weight="400" font-size="30" fill="var(--band-white)">HOLLOWMERE FURNISHINGS</text>
  </svg>
</main>
</body>
</html>
```